Printer Cartridges Supplier Namecard

Attached is my company logo and the design of my current namecard. I would like to have a more special look for it. Can have a little cuteness too rather than those normal standard feel. I'm a supplier mainly dealing with original and compatible printer toner cartridges, some other products like paper supplies as well.

Target Market(s)

Companies, businesses, corporates

Industry/Entity Type

It Company

Contact Information for Business Card

Logo, name, contact, address, supplies and maybe a slogan

Colors
85cae6
33a6d7
3176b5
0255a3
0792cd
85abd2

Requirements
Must have
• Logo, name, contact and address basic details.
• Must include some pictures, not just rearrange what I'm currently having.
Nice to have
• Be creative and bold, a diiferent traditional feel.

```html
<!DOCTYPE html>
<html lang="en">
<head>
<meta charset="utf-8">
<title>Tonerwell Namecard</title>
<link rel="stylesheet" href="https://fonts.googleapis.com/css2?family=Roboto:wght@400&family=Work+Sans:wght@400;500&display=swap">
<style>
  :root {
    --backdrop: #1c1c1d;
    --card-white: #ffffff;
    --card-grey: #5a5b5d;
    --brand-blue: #5db3e3;
    --ink-dark: #3d3d3f;
    --ink-mid: #555658;
    --band-grey: #5b5c5e;
    --url-light: #e6e6e6;
    --faint-tone: #f1f1f2;
  }
  * { margin: 0; padding: 0; box-sizing: border-box; }
  html, body {
    width: 1200px; height: 897px; overflow: hidden;
    background: var(--backdrop);
    font-family: "Work Sans", sans-serif;
  }
  .card {
    position: absolute; left: 303px; width: 595px; height: 339px;
    border-radius: 20px; overflow: hidden;
  }
  .card-front { top: 92px; background: var(--card-white); }
  .card-back { top: 469px; background: var(--card-grey); }

  .front-artwork {
    position: absolute; left: 300px; top: -40px; width: 330px; height: 300px;
    background: radial-gradient(circle at 60% 45%, var(--faint-tone) 0%, rgba(241,241,242,0.6) 40%, rgba(255,255,255,0) 70%);
  }

  .wordmark { position: absolute; display: flex; align-items: center; }
  .wordmark-square { background: var(--brand-blue); border-radius: 6px; flex: none; }
  .wordmark-text { display: flex; flex-direction: column; }
  .wordmark-name { font-family: "Work Sans", sans-serif; font-weight: 400; line-height: 1; }
  .wordmark-slogan { font-family: "Work Sans", sans-serif; font-weight: 400; white-space: nowrap; }

  .front-mark { left: 38px; top: 138px; gap: 10px; }
  .front-mark .wordmark-square { width: 62px; height: 62px; }
  .front-mark .wordmark-name { font-size: 38px; color: var(--ink-mid); letter-spacing: -0.5px; }
  .front-mark .wordmark-slogan { font-size: 7.4px; color: var(--ink-mid); margin-top: 3px; }

  .divider {
    position: absolute; left: 306px; top: 90px; width: 2px; height: 160px;
    background: var(--brand-blue);
  }

  .contact { position: absolute; left: 339px; top: 87px; color: var(--ink-dark); position: absolute; }
  .person-name {
    font-family: "Roboto", sans-serif; font-size: 20px; color: var(--brand-blue);
    text-transform: uppercase; line-height: 24px;
  }
  .person-role { font-size: 14.5px; letter-spacing: 0.8px; line-height: 18px; }
  .person-mobile { font-size: 14.5px; letter-spacing: 0.8px; line-height: 18px; }
  .person-mobile .label { color: var(--brand-blue); }
  .address { margin: 10px 0 0 3px; font-size: 14.5px; line-height: 17px; letter-spacing: 0.2px; }
  .channels { list-style: none; margin-top: 13px; font-size: 14.5px; line-height: 17.5px; }
  .channels li { display: flex; align-items: center; gap: 9px; }
  .channels svg { width: 8px; height: 8px; flex: none; }

  .front-bands { position: absolute; left: 0; bottom: 0; width: 595px; height: 27px; }

  .back-mark { left: 50%; top: 125px; transform: translateX(-50%); gap: 14px; }
  .back-mark .wordmark-square { width: 86px; height: 86px; border-radius: 8px; }
  .back-mark .wordmark-name { font-size: 60px; color: var(--card-white); letter-spacing: -0.5px; }
  .back-mark .wordmark-slogan { font-size: 11px; color: var(--card-white); margin-top: 4px; }

  .back-url {
    position: absolute; left: 0; right: 0; top: 296px; text-align: center;
    font-size: 14px; color: var(--url-light);
  }
</style>
</head>
<body>
  <section class="card card-front">
    <div class="front-artwork" role="img" aria-label="Faint printer cartridge artwork"></div>
    <div class="wordmark front-mark">
      <span class="wordmark-square"></span>
      <span class="wordmark-text">
        <span class="wordmark-name">tonerwell</span>
        <span class="wordmark-slogan">Compatible printer ink and toner solutions</span>
      </span>
    </div>
    <div class="divider"></div>
    <div class="contact">
      <p class="person-name">Maya Lorne</p>
      <p class="person-role">Sales Executive</p>
      <p class="person-mobile"><span class="label">HP</span> 8140 3376</p>
      <p class="address">41A Kestrel Park Avenue<br>05-112 Singapore 530417</p>
      <ul class="channels">
        <li><svg viewBox="0 0 8 8"><path d="M2 0.5 L3.2 2.2 L2.4 3 Q3.2 4.8 5 5.6 L5.8 4.8 L7.5 6 L6.6 7.5 Q1 6.5 0.5 1.4 Z" fill="#5db3e3"/></svg>961-304-5518</li>
        <li><svg viewBox="0 0 8 8"><rect x="0.5" y="1.5" width="7" height="5" fill="none" stroke="#5db3e3" stroke-width="0.9"/><path d="M0.5 1.5 L4 4.5 L7.5 1.5" fill="none" stroke="#5db3e3" stroke-width="0.9"/></svg>maya@tonerwell.sg</li>
        <li><svg viewBox="0 0 8 8"><circle cx="4" cy="4" r="3.5" fill="none" stroke="#5db3e3" stroke-width="0.8"/><ellipse cx="4" cy="4" rx="1.5" ry="3.5" fill="none" stroke="#5db3e3" stroke-width="0.7"/><path d="M0.5 4 H7.5" stroke="#5db3e3" stroke-width="0.7"/></svg>www.tonerwell.sg</li>
      </ul>
    </div>
    <svg class="front-bands" viewBox="0 0 595 27" preserveAspectRatio="none" aria-hidden="true">
      <polygon points="0,14 312,14 299,27 0,27" fill="var(--band-grey)"/>
      <polygon points="333,0 595,0 595,27 305,27" fill="var(--brand-blue)"/>
    </svg>
  </section>

  <section class="card card-back">
    <div class="wordmark back-mark">
      <span class="wordmark-square"></span>
      <span class="wordmark-text">
        <span class="wordmark-name">tonerwell</span>
        <span class="wordmark-slogan">Compatible printer ink and toner solutions</span>
      </span>
    </div>
    <p class="back-url">www.tonerwell.sg</p>
  </section>
</body>
</html>
```